Design a Travel and Tourism website

We would like a freelancer to design a website that is essentially easy to use and navigate database providing local information for Travelers about destination countries.

We proposed website would discuss different rates, fees, visa requirement, resort locations, cheap flights, etc. This website should be elegant and modern. Our business name is rovanix.
Some reference websites are zemplorift.ca, brindlefoxhaven.com,
There should be a forum in the website where travell\ers discuss about their first hand tranvel experience to such destinations.

Tourism

```html
<!DOCTYPE html>
<html lang="en">
<head>
<meta charset="utf-8">
<title>Rovanix — Travel and Tourism</title>
<link href="https://fonts.googleapis.com/css2?family=Ubuntu:wght@400;500;700&family=Open+Sans:wght@400;600;700&display=swap" rel="stylesheet">
<style>
:root{
  --blue:#3fb6e6;
  --orange:#f8a200;
  --ink:#222;
  --panel:rgba(22,22,22,.88);
  --line:#5a5a5a;
  --muted:#d8d8d8;
  --band:#f3f3f3;
  --white:#fff;
}
*{box-sizing:border-box;margin:0;padding:0}
html,body{width:696px;height:1200px;overflow:hidden;background:var(--white)}
body{position:relative;font-family:"Open Sans",sans-serif;color:var(--ink)}
.abs{position:absolute}
svg{display:block}

/* hero */
.hero-photo{left:0;top:0;width:696px;height:418px;
  background:radial-gradient(ellipse at 85% 55%,#f0a432 0%,#c0661c 30%,#6a3a18 60%,#2a1a10 100%)}
.logo{font-family:"Ubuntu",sans-serif;font-weight:500;font-size:20px;color:var(--white);left:99px;top:14px}
.nav{top:23px;left:280px;font-size:7px}
.nav span{color:var(--white);position:absolute;white-space:nowrap}
.nav span.active::after{content:"";position:absolute;left:0;right:0;top:13px;height:1px;background:var(--blue)}
.search-dot{left:579px;top:21px;width:16px;height:16px;border-radius:50%;background:var(--blue)}

.panel{left:118px;top:85px;width:460px;height:274px;background:var(--panel)}
.tab{width:54px;height:40px;border:1px solid #cfcfcf;top:107px;color:var(--white);font-size:5.5px;text-align:center;padding-top:8px}
.tab svg{margin:0 auto 4px}
.tab.on{background:var(--blue);border-color:var(--blue)}
.label{font-size:5.8px;color:var(--muted);white-space:nowrap}
.field{border:1px solid var(--line);height:28px;font-size:5px;color:var(--muted);display:flex;align-items:center;padding-left:9px;gap:6px}
.caret{position:absolute;right:8px;top:11px}
.check{left:131px;top:282px;width:8px;height:8px;background:var(--blue);border-radius:1px}
.link{font-size:5.5px;color:var(--white);text-decoration:underline;white-space:nowrap}
.btn-search{left:333px;top:306px;width:61px;height:23px;background:var(--blue);color:var(--white);font-size:7px;font-weight:700;display:flex;align-items:center;justify-content:center}
.dot{top:379px;width:5px;height:5px;border-radius:50%;background:var(--white)}
.dot.on{background:var(--blue)}

/* destinations */
.section-title{font-family:"Ubuntu",sans-serif;font-weight:500;font-size:13px;width:696px;text-align:center;left:0}
.card{width:157px;height:102px}
.card-photo{position:absolute;inset:0}
.badge{position:absolute;left:9px;top:9px;width:52px;height:52px;border-radius:50%;background:var(--orange);color:var(--white);text-align:center;font-family:"Ubuntu",sans-serif;padding-top:11px}
.badge small{display:block;font-size:5px;line-height:7px}
.badge b{display:block;font-size:11px;color:#2b2b2b;font-weight:700;margin-top:1px}
.card-foot{position:absolute;left:0;right:0;bottom:0;height:22px;display:flex}
.place{width:89px;background:rgba(20,20,20,.85);color:var(--white);font-size:5.5px;display:flex;align-items:center;padding-left:11px;white-space:nowrap}
.offer{flex:1;background:var(--blue);color:var(--white);font-family:"Ubuntu",sans-serif;font-size:7.5px;font-weight:700;display:flex;align-items:center;justify-content:center}
.btn-view{left:278px;top:739px;width:140px;height:24px;background:var(--blue);color:var(--white);font-family:"Ubuntu",sans-serif;font-size:7px;font-weight:500;display:flex;align-items:center;justify-content:center}

/* countries */
.band{left:0;top:782px;width:696px;height:170px;background:var(--band)}
.country-map{top:852px;height:50px;background:#111;border-radius:40% 55% 45% 50%}
.country-map.hl{background:var(--blue)}
.country-name{top:920px;font-size:5.5px;font-weight:700;width:80px;text-align:center}

/* ad */
.ad{left:137px;top:979px;width:421px;height:39px;background:linear-gradient(90deg,#3b3a22 0%,#6d7a3a 45%,#8fa0a8 70%,#4f5a3c 100%);overflow:hidden}
.ad-head{left:30px;top:4px;color:var(--white);font-family:"Ubuntu",sans-serif;font-weight:700;line-height:1;white-space:nowrap}
.ad-head .a{font-size:11px;display:block;padding-left:10px}
.ad-head .b{font-size:17px}
.ad-cta{left:158px;top:12px;height:14px;padding:0 6px;background:var(--orange);color:var(--white);font-size:6.5px;font-weight:700;display:flex;align-items:center;border-radius:2px;white-space:nowrap}
.ad-car{left:292px;top:8px;width:62px;height:26px;border-radius:40% 40% 20% 20%;background:#2f4e6e}
.ad-badge{left:386px;top:5px;width:28px;height:28px;background:var(--white);border-radius:3px}

/* footer */
.foot-logo{left:99px;top:1048px;font-family:"Ubuntu",sans-serif;font-weight:500;font-size:19px;color:var(--blue)}
.foot-head{top:1050px;font-size:6.5px;color:var(--blue)}
.foot-list{top:1075px;list-style:none;font-size:6.5px;line-height:13px;color:#333}
.social{top:1077px;width:8px;height:8px;background:#3a4a5a;border-radius:1px}
.rule{left:0;top:1175px;width:696px;height:1px;background:#dcdcdc}
.copy{left:0;top:1186px;width:696px;text-align:center;font-size:5.5px;color:#444}
</style>
</head>
<body>

<!-- hero -->
<div class="abs hero-photo" role="img" aria-label="Hiker with backpack standing on a rocky hilltop at sunset"></div>
<div class="abs logo">Rovanix</div>
<nav class="abs nav">
  <span class="active" style="left:0">Home</span>
  <span style="left:37px">Rates</span>
  <span style="left:71px">Fees</span>
  <span style="left:103px">Visa Requirement</span>
  <span style="left:175px">Resort Locations</span>
  <span style="left:244px">Cheap Flights</span>
</nav>
<div class="abs search-dot"><svg width="16" height="16" viewBox="0 0 16 16"><circle cx="7.5" cy="7.5" r="2" fill="none" stroke="#fff" stroke-width="1"/><line x1="9" y1="9" x2="10.5" y2="10.5" stroke="#fff" stroke-width="1"/></svg></div>

<section class="abs panel"></section>
<div class="abs tab on" style="left:131px"><svg width="12" height="11" viewBox="0 0 12 11"><path d="M1 5h10M7 1l2 4-2 5M4 5 3 3M4 5 3 8" stroke="#fff" stroke-width="1.4" fill="none"/></svg>Flights</div>
<div class="abs tab" style="left:191px"><svg width="12" height="12" viewBox="0 0 12 12"><path d="M3 1v10M1 1v3h4V1M9 1c-2 0-2 5 0 5v5" stroke="#3fb6e6" stroke-width="1.4" fill="none"/></svg>Hotels</div>
<div class="abs tab" style="left:251px"><svg width="14" height="11" viewBox="0 0 14 11"><rect x="1" y="4" width="12" height="5" rx="1" fill="#3fb6e6"/><path d="M3 4l1.5-3h5L11 4" stroke="#3fb6e6" stroke-width="1.3" fill="none"/></svg>Car Rental</div>
<div class="abs tab" style="left:310px"><svg width="11" height="12" viewBox="0 0 11 12"><rect x="1.5" y="1" width="8" height="8" rx="2" fill="none" stroke="#3fb6e6" stroke-width="1.3"/><path d="M3 11l1-2M8 11 7 9M2 5h7" stroke="#3fb6e6" stroke-width="1.2"/></svg>Train</div>
<div class="abs tab" style="left:370px"><svg width="11" height="12" viewBox="0 0 11 12"><rect x="1.5" y="1" width="8" height="9" rx="2" fill="none" stroke="#3fb6e6" stroke-width="1.3"/><path d="M2 6h7" stroke="#3fb6e6" stroke-width="1.2"/></svg>Bus</div>

<div class="abs label" style="left:130px;top:168px">Flying From</div>
<div class="abs label" style="left:353px;top:168px">Flying To</div>
<div class="abs field" style="left:131px;top:185px;width:211px"><svg width="5" height="7" viewBox="0 0 5 7"><path d="M2.5 7C1 5 0 3.6 0 2.5a2.5 2.5 0 0 1 5 0C5 3.6 4 5 2.5 7z" fill="#3fb6e6"/></svg>City or Airport</div>
<div class="abs field" style="left:353px;top:185px;width:210px"><svg width="5" height="7" viewBox="0 0 5 7"><path d="M2.5 7C1 5 0 3.6 0 2.5a2.5 2.5 0 0 1 5 0C5 3.6 4 5 2.5 7z" fill="#3fb6e6"/></svg>City or Airport</div>

<div class="abs label" style="left:130px;top:224px">Departing</div>
<div class="abs label" style="left:246px;top:224px">Returning</div>
<div class="abs label" style="left:363px;top:224px">Rooms</div>
<div class="abs label" style="left:435px;top:224px">Adults(18+)</div>
<div class="abs label" style="left:508px;top:224px">Children (1-17)</div>
<div class="abs field" style="left:131px;top:241px;width:106px"><svg width="7" height="7" viewBox="0 0 7 7"><rect x=".5" y="1" width="6" height="5.5" fill="none" stroke="#3fb6e6"/><path d="M.5 3h6" stroke="#3fb6e6"/></svg></div>
<div class="abs field" style="left:247px;top:241px;width:106px"><svg width="7" height="7" viewBox="0 0 7 7"><rect x=".5" y="1" width="6" height="5.5" fill="none" stroke="#3fb6e6"/><path d="M.5 3h6" stroke="#3fb6e6"/></svg></div>
<div class="abs field" style="left:364px;top:241px;width:54px"><svg class="caret" width="6" height="4" viewBox="0 0 6 4"><path d="M.5.5 3 3 5.5.5" stroke="#ddd" fill="none"/></svg></div>
<div class="abs field" style="left:436px;top:241px;width:54px"><svg class="caret" width="6" height="4" viewBox="0 0 6 4"><path d="M.5.5 3 3 5.5.5" stroke="#ddd" fill="none"/></svg></div>
<div class="abs field" style="left:509px;top:241px;width:54px"><svg class="caret" width="6" height="4" viewBox="0 0 6 4"><path d="M.5.5 3 3 5.5.5" stroke="#ddd" fill="none"/></svg></div>

<div class="abs check"><svg width="8" height="8" viewBox="0 0 8 8"><path d="M1.8 4 3.4 5.6 6.3 2.4" stroke="#fff" stroke-width="1" fill="none"/></svg></div>
<div class="abs label" style="left:142px;top:283px;color:#fff">I only need a hotel for part of my stay</div>

<div class="abs field" style="left:131px;top:306px;width:119px;height:23px;color:#fff;font-size:5.5px">Economy /Coach<svg class="caret" style="top:9px" width="6" height="4" viewBox="0 0 6 4"><path d="M.5.5 3 3 5.5.5" stroke="#ddd" fill="none"/></svg></div>
<div class="abs link" style="left:258px;top:314px">Advance Options &gt;&gt;</div>
<div class="abs btn-search">SEARCH</div>

<div class="abs dot on" style="left:324px"></div>
<div class="abs dot" style="left:339px"></div>
<div class="abs dot" style="left:353px"></div>
<div class="abs dot" style="left:367px"></div>

<!-- destinations -->
<h2 class="abs section-title" style="top:458px">DESTINATIONS</h2>

<article class="abs card" style="left:99px;top:500px">
  <div class="card-photo" role="img" aria-label="Suspension bridge and city skyline at sunset" style="background:linear-gradient(135deg,#2b3f7a,#b86a6a 55%,#f1b070)"></div>
  <div class="badge"><small>TOUR<br>STARTS@</small><b>$723</b></div>
  <div class="card-foot"><div class="place">Newyork | USA</div><div class="offer">15% OFFER</div></div>
</article>
<article class="abs card" style="left:269px;top:500px">
  <div class="card-photo" role="img" aria-label="City skyline with TV tower by the river" style="background:linear-gradient(180deg,#6fa4d8,#b9c2c4 50%,#8b6b5a)"></div>
  <div class="badge"><small>TOUR<br>STARTS@</small><b>$723</b></div>
  <div class="card-foot"><div class="place">Berlin | GERMAN</div><div class="offer">25% OFFER</div></div>
</article>
<article class="abs card" style="left:438px;top:500px">
  <div class="card-photo" role="img" aria-label="Limestone island rising from a tropical bay" style="background:linear-gradient(180deg,#6aa8d8,#5b8a4a 55%,#2bb3b8)"></div>
  <div class="badge"><small>TOUR<br>STARTS@</small><b>$723</b></div>
  <div class="card-foot"><div class="place">Phunket | THAILAND</div><div class="offer">10% OFFER</div></div>
</article>
<article class="abs card" style="left:99px;top:617px">
  <div class="card-photo" role="img" aria-label="Hot air balloons over temples at sunset" style="background:linear-gradient(180deg,#5a4a7a,#e07a3a 60%,#2a1a1a)"></div>
  <div class="badge"><small>TOUR<br>STARTS@</small><b>$723</b></div>
  <div class="card-foot"><div class="place">Myanmar &nbsp;| BURMA</div><div class="offer">15% OFFER</div></div>
</article>
<article class="abs card" style="left:269px;top:617px">
  <div class="card-photo" role="img" aria-label="Temple spires by the river at dusk" style="background:linear-gradient(180deg,#4a6aa0,#e08a4a 55%,#3a2a2a)"></div>
  <div class="badge"><small>TOUR<br>STARTS@</small><b>$723</b></div>
  <div class="card-foot"><div class="place">Bangkok | THAILAND</div><div class="offer">25% OFFER</div></div>
</article>
<article class="abs card" style="left:438px;top:617px">
  <div class="card-photo" role="img" aria-label="Sailing boats anchored in a turquoise cove" style="background:linear-gradient(180deg,#8ec4ea,#4a8a4a 40%,#1ec0e0)"></div>
  <div class="badge"><small>TOUR<br>STARTS@</small><b>$723</b></div>
  <div class="card-foot"><div class="place">Paxos Island &nbsp;| GREECE</div><div class="offer">10% OFFER</div></div>
</article>

<div class="abs btn-view">VIEW YOUR DESTINATIONS</div>

<!-- countries -->
<section class="abs band"></section>
<h2 class="abs section-title" style="top:808px">COUNTRIES</h2>
<div class="abs country-map hl" style="left:100px;width:65px;height:42px;top:856px" role="img" aria-label="Map of Iceland"></div>
<div class="abs country-map" style="left:210px;width:48px;height:46px" role="img" aria-label="Map of France"></div>
<div class="abs country-map" style="left:300px;width:28px;height:48px" role="img" aria-label="Map of the UK"></div>
<div class="abs country-map" style="left:376px;width:44px;height:46px" role="img" aria-label="Map of Greece"></div>
<div class="abs country-map" style="left:450px;width:38px;height:50px" role="img" aria-label="Map of Italy"></div>
<div class="abs country-map" style="left:522px;width:70px;height:44px;top:853px" role="img" aria-label="Map of Switzerland"></div>
<div class="abs country-name" style="left:94px">ICELAND</div>
<div class="abs country-name" style="left:197px">FRANCE</div>
<div class="abs country-name" style="left:277px">UK</div>
<div class="abs country-name" style="left:365px">GREECE</div>
<div class="abs country-name" style="left:436px">ITALY</div>
<div class="abs country-name" style="left:518px">SWITZERLAND</div>

<!-- advert -->
<aside class="abs ad" role="img" aria-label="Car trade-in advertisement with a car on a country road">
  <div class="abs ad-head"><span class="a">SWAP YOUR CAR</span><span class="b">IN MINUTES</span></div>
  <div class="abs ad-cta">SEE YOUR QUICK QUOTE!</div>
  <div class="abs ad-car"></div>
  <div class="abs ad-badge"></div>
</aside>

<!-- footer -->
<div class="abs foot-logo">Rovanix</div>
<div class="abs foot-head" style="left:226px">Quick Links</div>
<div class="abs foot-head" style="left:354px">Other Links</div>
<div class="abs foot-head" style="left:466px">Connect With Us</div>
<ul class="abs foot-list" style="left:228px">
  <li>Home</li><li>Rates</li><li>Fees</li><li>Visa Requirement</li><li>Resort Locations</li><li>Cheap Flights</li>
</ul>
<ul class="abs foot-list" style="left:354px">
  <li>Legal</li><li>Contact Us</li><li>Privacy</li><li>Terms &amp; Conditions</li><li>Security</li><li>Cookie</li>
</ul>
<div class="abs social" style="left:470px;background:var(--blue)"></div>
<div class="abs social" style="left:484px"></div>
<div class="abs social" style="left:498px"></div>
<div class="abs rule"></div>
<div class="abs copy">© 2017 Company Name &nbsp;| &nbsp;All Rights Reserved</div>

</body>
</html>
```